New Interrior Decoration company needs new website

We need a website for our new company specialising in interior decoration to residential and commercial markets.
We supply and install decorative and printed films for office and home decoration such as feature walls.
We would like to keep the design simple and clean.

Target Market(s)

Architects and interior designaers

Industry/Entity Type

It Company

Number of Pages Required

5+ page

Font styles to use
Sans Serif

Requirements
Must have
• Home page,
• Services/products page (split into commercial and residential)
• Gallery (split into commercial and residential)
• contact form and page
Nice to have
• Very clean and minimalistic design.

```html
<!DOCTYPE html>
<html lang="en">
<head>
<meta charset="utf-8">
<title>Lumen Line Interiors</title>
<link href="https://fonts.googleapis.com/css2?family=Lato:wght@400;700;900&family=Open+Sans:wght@400;600;700&family=Raleway:wght@300;400&display=swap" rel="stylesheet">
<style>
  :root {
    --blue: #0a5bbf;
    --dark: #3a3a3a;
    --darker: #333333;
    --ink: #333333;
    --muted: #555555;
    --white: #ffffff;
    --rule: #555555;
  }
  * { box-sizing: border-box; margin: 0; padding: 0; }
  html, body { width: 697px; height: 1200px; overflow: hidden; background: var(--white); }
  body { font-family: "Open Sans", sans-serif; color: var(--ink); }
  h1, h2 { font-weight: 400; }
  .page { position: relative; width: 697px; height: 1200px; overflow: hidden; }
  .abs { position: absolute; }

  /* Hero */
  .hero { left: 0; top: 0; width: 697px; height: 428px; }
  .hero-photo { position: absolute; inset: 0;
    background: radial-gradient(ellipse 60% 45% at 55% 20%, #f4f4f2 0%, #e6e7e6 55%, #d3d6d6 100%); }
  .brand { position: absolute; left: 0; right: 0; top: 124px; display: flex; justify-content: center; align-items: center; gap: 12px; }
  .brand-mark { width: 42px; height: 42px; background: var(--blue); }
  .brand-name { font-family: "Lato", sans-serif; font-weight: 900; font-size: 36px; line-height: 1; color: var(--darker); letter-spacing: -0.5px; }
  .tagline { position: absolute; left: 0; right: 0; top: 226px; text-align: center; font-family: "Lato", sans-serif; font-weight: 900; font-size: 22px; color: var(--blue); letter-spacing: -0.6px; }
  .hero-btn { position: absolute; left: 291px; top: 278px; width: 115px; height: 33px; background: var(--blue); color: var(--white); border-radius: 2px;
    font-family: "Open Sans", sans-serif; font-weight: 700; font-size: 13px; display: flex; align-items: center; justify-content: center; }

  /* Nav */
  .main-nav { left: 0; top: 428px; width: 697px; height: 36px; background: var(--blue); display: flex; padding-left: 45px; }
  .main-nav a { color: var(--white); text-decoration: none; font-family: "Raleway", sans-serif; font-size: 12.5px; height: 36px; display: flex; align-items: center; padding: 0 20px; }
  .main-nav a.is-active { background: var(--dark); }

  /* Welcome */
  .welcome-title { left: 0; top: 494px; width: 697px; text-align: center; font-family: "Raleway", sans-serif; font-size: 24px; color: var(--ink); }
  .welcome-title span { color: var(--blue); }
  .welcome-text { left: 98px; top: 535px; width: 502px; text-align: center; font-size: 9.2px; line-height: 14.5px; color: var(--muted); }

  .service { top: 600px; height: 82px; }
  .service-photo { position: absolute; left: 0; top: 0; width: 120px; height: 82px; }
  .service-body { position: absolute; left: 130px; top: -2px; width: 200px; }
  .service-title { font-family: "Raleway", sans-serif; font-size: 16px; color: var(--ink); margin-bottom: 3px; white-space: nowrap; }
  .service-text { font-size: 9.2px; line-height: 14.5px; color: var(--muted); width: 160px; }
  .read-more { display: inline-flex; align-items: center; gap: 4px; margin-top: 6px; font-family: "Raleway", sans-serif; font-size: 11px; color: var(--blue); }

  /* Call band */
  .call-band { left: 0; top: 722px; width: 697px; height: 84px; background: var(--dark); }
  .call-band svg.band-shape { position: absolute; left: 0; top: 0; }
  .call-label { position: absolute; left: 45px; top: 31px; font-family: "Raleway", sans-serif; font-size: 15px; color: var(--white); }
  .call-icon { position: absolute; left: 161px; top: 22px; width: 37px; height: 37px; border: 1.5px solid var(--white); border-radius: 50%; display: flex; align-items: center; justify-content: center; }
  .call-number { position: absolute; left: 205px; top: 28px; font-family: "Open Sans", sans-serif; font-weight: 700; font-size: 19px; color: var(--white); }
  .call-note { position: absolute; left: 383px; top: 14px; width: 260px; font-size: 9.2px; line-height: 14.5px; color: var(--white); }
  .call-mail { position: absolute; left: 382px; top: 50px; display: flex; align-items: center; gap: 6px; font-size: 10px; color: var(--white); }

  /* Gallery */
  .gallery-title { left: 0; top: 838px; width: 697px; text-align: center; font-family: "Raleway", sans-serif; font-size: 24px; color: var(--ink); }
  .gallery-title span { color: var(--blue); }
  .gallery-tabs { left: 234px; top: 874px; display: flex; gap: 12px; }
  .gallery-tab { width: 109px; height: 30px; display: flex; align-items: center; justify-content: center; font-family: "Raleway", sans-serif; font-size: 14px; color: var(--white); background: var(--dark); }
  .gallery-tab.is-active { background: var(--blue); }
  .gallery-item { top: 923px; width: 136px; height: 91px; }

  /* Footer */
  .site-footer { left: 0; top: 1062px; width: 697px; height: 138px; background: var(--dark); color: var(--white); }
  .footer-nav { position: absolute; left: 46px; top: 22px; display: flex; gap: 20px; font-size: 11.5px; }
  .social { position: absolute; left: 496px; top: 16px; display: flex; gap: 16px; }
  .social span { width: 27px; height: 27px; border: 1px solid var(--white); border-radius: 2px; display: flex; align-items: center; justify-content: center; }
  .social span::after { content: ""; width: 9px; height: 9px; border-radius: 50%; background: var(--white); }
  .social span:first-child { background: var(--white); }
  .social span:first-child::after { background: var(--dark); }
  .footer-rule { position: absolute; left: 46px; top: 58px; width: 607px; height: 1px; background: var(--rule); }
  .footer-heading { position: absolute; left: 46px; top: 70px; font-size: 11.5px; }
  .footer-item { position: absolute; top: 90px; display: flex; align-items: center; gap: 6px; font-size: 9.2px; line-height: 13.5px; white-space: nowrap; }
  .footer-icon { width: 24px; height: 24px; background: var(--white); border-radius: 2px; display: flex; align-items: center; justify-content: center; flex: none; }
  .copyright { position: absolute; left: 520px; top: 92px; font-size: 9px; line-height: 14.5px; white-space: nowrap; }
</style>
</head>
<body>
<div class="page">

  <header class="hero abs">
    <div class="hero-photo" role="img" aria-label="Bright white kitchen and dining interior with pendant lamp, long table and grey chairs"></div>
    <div class="brand">
      <span class="brand-mark"></span>
      <span class="brand-name">LUMEN LINE<br>INTERIORS</span>
    </div>
    <p class="tagline">LOREM IPSUM IS DUMMY TEXT.</p>
    <a class="hero-btn">CONTACT US</a>
  </header>

  <nav class="main-nav abs">
    <a class="is-active">HOME</a>
    <a>ABOUT</a>
    <a>SERVICES</a>
    <a>GALLERY</a>
    <a>CONTACT</a>
  </nav>

  <h1 class="welcome-title abs">WELCOME TO <span>LUMEN LINE INTERIORS</span></h1>
  <p class="welcome-text abs">Lorem Ipsum is simply dummy text of the printing and typesetting industry. Lorem Ipsum has been the industry's standard dummy text ever since the 1500s, when an unknown printer took a galley of type and scrambled it to make a type specimen book.</p>

  <article class="service abs" style="left:46px;">
    <div class="service-photo" role="img" aria-label="Residential room with grey feature wall, shelf and black pendant lamp" style="background:linear-gradient(160deg,#6f7475 0%,#8b8f8e 50%,#b9bab4 100%);"></div>
    <div class="service-body">
      <h2 class="service-title">Residential Interiors</h2>
      <p class="service-text">Lorem Ipsum is simply dummy text of the printing and typesetting industry Lorem Ipsum...</p>
      <span class="read-more">READ MORE
        <svg width="9" height="9" viewBox="0 0 9 9"><path d="M1 1l3 3.5L1 8M5 1l3 3.5L5 8" fill="none" stroke="#0a5bbf" stroke-width="1.4"/></svg></span>
    </div>
  </article>

  <article class="service abs" style="left:365px;">
    <div class="service-photo" role="img" aria-label="Office glass partition with printed film of red and tan circles" style="background:linear-gradient(90deg,#6a655f 0%,#d4d1cc 30%,#e4e1dc 65%,#b9aa9a 100%);"></div>
    <div class="service-body">
      <h2 class="service-title">Commercial Interiors</h2>
      <p class="service-text">Lorem Ipsum is simply dummy text of the printing and typesetting industry Lorem Ipsum...</p>
      <span class="read-more">READ MORE
        <svg width="9" height="9" viewBox="0 0 9 9"><path d="M1 1l3 3.5L1 8M5 1l3 3.5L5 8" fill="none" stroke="#0a5bbf" stroke-width="1.4"/></svg></span>
    </div>
  </article>

  <section class="call-band abs">
    <svg class="band-shape" width="360" height="84" viewBox="0 0 360 84">
      <polygon points="0,0 341,0 357,42 341,84 0,84" fill="#ffffff"/>
      <polygon points="0,0 336,0 352,42 336,84 0,84" fill="#0a5bbf"/>
    </svg>
    <span class="call-label">CALL US NOW!</span>
    <span class="call-icon">
      <svg width="16" height="16" viewBox="0 0 24 24"><path d="M6.6 10.8a15.1 15.1 0 006.6 6.6l2.2-2.2c.3-.3.7-.4 1-.2 1.1.4 2.3.6 3.6.6.6 0 1 .4 1 1V20c0 .6-.4 1-1 1A17 17 0 013 4c0-.6.4-1 1-1h3.5c.6 0 1 .4 1 1 0 1.3.2 2.5.6 3.6.1.3 0 .7-.2 1z" fill="#ffffff"/></svg>
    </span>
    <span class="call-number">123 456 7890</span>
    <p class="call-note">Lorem Ipsum is simply dummy text of the printing and typesetting industry lorem Ipsum has been.</p>
    <span class="call-mail">
      <svg width="12" height="10" viewBox="0 0 12 10"><rect x="0.6" y="0.6" width="10.8" height="8.8" fill="none" stroke="#fff" stroke-width="1.1"/><path d="M0.6 0.8L6 5.5l5.4-4.7" fill="none" stroke="#fff" stroke-width="1.1"/></svg>
      Info@lumenlineinteriors.com
    </span>
  </section>

  <h2 class="gallery-title abs">LATEST <span>GALLERY</span></h2>
  <div class="gallery-tabs abs">
    <span class="gallery-tab is-active">Residential</span>
    <span class="gallery-tab">Commercial</span>
  </div>
  <div class="gallery-item abs" style="left:45px;background:linear-gradient(120deg,#c4a45e 0%,#b5ad78 45%,#c9553e 80%,#ddd6c8 100%);" role="img" aria-label="Living room with striped wood feature wall and red armchairs"></div>
  <div class="gallery-item abs" style="left:202px;background:linear-gradient(120deg,#3a2220 0%,#6e3520 45%,#b9aab4 75%,#4a3c3e 100%);" role="img" aria-label="Lounge chair in front of a dark rust textured wall and bookshelf"></div>
  <div class="gallery-item abs" style="left:359px;background:linear-gradient(120deg,#8a6a8c 0%,#c0625e 40%,#6a8cc0 72%,#dcdcda 100%);" role="img" aria-label="Meeting room with colourful printed cartoon wall film"></div>
  <div class="gallery-item abs" style="left:516px;background:linear-gradient(160deg,#6f7475 0%,#8b8f8e 50%,#b9bab4 100%);" role="img" aria-label="Residential room with grey feature wall, shelf and black pendant lamp"></div>

  <footer class="site-footer abs">
    <nav class="footer-nav"><span>Home</span><span>About</span><span>Services</span><span>Gallery</span><span>Contact</span></nav>
    <div class="social" aria-label="Social links"><span></span><span></span><span></span><span></span></div>
    <div class="footer-rule"></div>
    <p class="footer-heading">Contact Us</p>
    <div class="footer-item" style="left:46px;">
      <span class="footer-icon"><svg width="10" height="13" viewBox="0 0 10 13"><path d="M5 0.5A4.3 4.3 0 00.7 4.8C.7 8 5 12.5 5 12.5S9.3 8 9.3 4.8A4.3 4.3 0 005 .5z" fill="#3a3a3a"/><circle cx="5" cy="4.8" r="1.6" fill="#fff"/></svg></span>
      <span>Lorem Ipsum is dummy<br>text of the printing.</span>
    </div>
    <div class="footer-item" style="left:203px;">
      <span class="footer-icon"><svg width="13" height="13" viewBox="0 0 24 24"><path d="M6.6 10.8a15.1 15.1 0 006.6 6.6l2.2-2.2c.3-.3.7-.4 1-.2 1.1.4 2.3.6 3.6.6.6 0 1 .4 1 1V20c0 .6-.4 1-1 1A17 17 0 013 4c0-.6.4-1 1-1h3.5c.6 0 1 .4 1 1 0 1.3.2 2.5.6 3.6.1.3 0 .7-.2 1z" fill="#3a3a3a"/></svg></span>
      <strong>123 456 7890</strong>
    </div>
    <div class="footer-item" style="left:335px;font-size:9px;">
      <span class="footer-icon"><svg width="12" height="10" viewBox="0 0 12 10"><rect x="0.6" y="0.6" width="10.8" height="8.8" fill="none" stroke="#3a3a3a" stroke-width="1.1"/><path d="M0.6 0.8L6 5.5l5.4-4.7" fill="none" stroke="#3a3a3a" stroke-width="1.1"/></svg></span>
      <span>Info@lumenlineinteriors.com</span>
    </div>
    <p class="copyright">© <strong>LUMEN LINE INTERIORS</strong> - 2016.<br>All Rights Reserved.</p>
  </footer>

</div>
</body>
</html>
```